Need App for Impact Related Events

My app is to help with internal events. When you enter the prompted event code the next screen shows you everyone currently at the event. It will give you the ability to Start a conversation with someone you met at that event, or signal it is your turn to send a message. The next screen is a message thread with that person. I am looking for a design that incorporates the colors and ‘feel good’ emotion of our logo. I have pieced together a pretty good interpretation of what I’m looking for in the attached mockup by slicing and dicing designs. I also attached our logo mascot.Screens (see attached mockups)

Note 1: I do not like the picture on the screen used in screen one because it makes it seem like a dating app. I attached an alternative photo that can be used or present different ideas.

Note 2: On the login/signup screen (screen 2) I need an additional first and last name for login, you can try to fit this on one login screen or present a two step signup screen where that is presented in the second screen.

READ MOCKUP GUIDELINES UNDER Must Haves

Target Market(s)

People attending internal social impact events

Industry/Entity Type

Charity

Font styles to use
Sans Serif

Colors
86cfc6

Requirements
Must have
• Follow the screen mockups attached to project
• PLEASE READ
• I have provided a relatively close design of what I’m looking for in the mockups. Some screens need to be followed more closely to my design mockup than other. I have listed a guide below how how closely you should follow my mockup design exactly. Overall I would like to see some ideas of incorporating a few accent colors so it doesn’t appear SO Blue. I also attached some app inspiration designs I found from around the web
• Screen Mockup Guideline Follow %
• Screen 1: 65% - mostly on target, would like to see ways to make it not SO Blue and possibly creative places to add some explainer text describing the app
• Screen 2: 50% - general design idea is here, but more open
• Screen 3: 35% - a lot more room for design influence
• Screen 4: 70% - mostly on target, a little room for design influence/color scheme ideas
• Screen 5-6: 25% - a lot of room for design change/ideas/influence
• Screen 7-8: 80% - already very close to what I need, maybe open to slight sizing and color scheme ideas
• Screen 9: 15% - the most open for influence, only the general functionality of the screen is communicated here
Nice to have
• Please Read Mockup Guideline above. In large part I am looking for something to use some nice accent colors so it is not overwhelmingly blue and bring the whole design into a seamless style.
Should not have

```html
<!DOCTYPE html>
<html lang="en">
<head>
<meta charset="utf-8">
<title>Password Recovery</title>
<link rel="stylesheet" href="https://fonts.googleapis.com/css2?family=Mulish:wght@400;600;700;800&family=Roboto:wght@400;500&display=swap">
<style>
  :root {
    --teal-bg: #74e1e0;
    --teal-deep: #169a9a;
    --teal-button: #00c8c6;
    --teal-fab: #2fd3d0;
    --field-line: rgba(255,255,255,0.55);
    --card: #ffffff;
    --ink: #2f3338;
    --ink-soft: #6b7075;
    --border: #e3e5e7;
    --kb-bg: #eef0f1;
    --kb-key: #202124;
    --kb-hint: #5f6368;
    --kb-space: #d7d9db;
    --kb-enter: #4a86e8;
    --divider: #c9cccf;
  }
  * { box-sizing: border-box; margin: 0; padding: 0; }
  html, body { width: 675px; height: 1200px; overflow: hidden; background: var(--teal-bg); }
  .screen {
    position: relative; width: 360px; height: 640px;
    transform: scale(1.875); transform-origin: 0 0;
    background: var(--teal-bg);
    font-family: "Mulish", "Helvetica Neue", Arial, sans-serif;
  }
  .back { position: absolute; left: 19px; top: 27px; width: 16px; height: 18px; }
  .login-title {
    position: absolute; left: 29px; top: 80px;
    font-size: 36px; font-weight: 800; color: var(--teal-deep);
  }
  .login-field {
    position: absolute; left: 30px; width: 300px; height: 38px;
    border: 1.5px solid var(--field-line); border-radius: 20px;
  }
  .login-field.email { top: 173px; }
  .login-field.password { top: 239px; }
  .forgot {
    position: absolute; right: 30px; top: 291px;
    font-size: 13px; font-weight: 800; color: var(--teal-deep);
  }
  .next-fab {
    position: absolute; left: 274px; top: 334px; width: 56px; height: 56px;
    border-radius: 50%; background: var(--teal-fab);
    display: flex; align-items: center; justify-content: center;
  }
  .recovery-card {
    position: absolute; left: 47px; top: 92px; width: 295px; height: 260px;
    background: var(--card); border-radius: 4px;
    box-shadow: 0 2px 10px rgba(0,80,80,0.12);
    text-align: center;
  }
  .recovery-title {
    margin-top: 14px; font-size: 20px; font-weight: 700; color: var(--ink);
    letter-spacing: 0.2px;
  }
  .email-input {
    position: absolute; left: 14px; top: 59px; width: 238px; height: 38px;
    border: 1px solid var(--border); border-radius: 4px;
    padding-left: 14px; text-align: left; line-height: 36px;
    font-size: 14px; color: var(--ink); font-weight: 400;
  }
  .recovery-note {
    position: absolute; left: 0; right: 0; top: 122px;
    font-size: 13px; line-height: 18px; color: var(--ink-soft);
  }
  .recover-button {
    position: absolute; left: 53px; top: 193px; width: 160px; height: 40px;
    border-radius: 4px; background: var(--teal-button);
    color: #fff; font-size: 12px; font-weight: 800; letter-spacing: 1px;
    line-height: 40px;
  }
  .keyboard {
    position: absolute; left: 0; top: 395px; width: 360px; height: 245px;
    background: var(--kb-bg);
    font-family: "Roboto", Arial, sans-serif; color: var(--kb-key);
  }
  .suggestions { position: relative; height: 40px; border-bottom: 1px solid #dfe1e3; }
  .suggestion { position: absolute; top: 12px; font-size: 15px; color: #3c4043; transform: translateX(-50%); }
  .suggestion-divider { position: absolute; top: 10px; width: 1px; height: 20px; background: var(--divider); }
  .mic { position: absolute; left: 336px; top: 12px; }
  .key-row { position: absolute; left: 0; width: 360px; height: 40px; display: flex; }
  .key {
    position: relative; width: 36px; height: 40px;
    display: flex; align-items: center; justify-content: center;
    font-size: 20px;
  }
  .key sup {
    position: absolute; top: 0; right: 4px; font-size: 9px; color: var(--kb-hint);
  }
  .row-1 { top: 51px; }
  .row-2 { top: 101px; padding-left: 18px; }
  .row-3 { top: 151px; }
  .row-4 { top: 197px; align-items: center; }
  .key.wide { width: 54px; }
  .key.symbols { width: 56px; font-size: 13px; }
  .key.comma { width: 28px; }
  .key.emoji { width: 40px; }
  .space-bar { width: 125px; height: 23px; margin: 0 8px 0 11px; background: var(--kb-space); border-radius: 3px; }
  .key.period { width: 36px; }
  .enter {
    width: 30px; height: 30px; border-radius: 50%; background: var(--kb-enter);
    display: flex; align-items: center; justify-content: center; margin-left: 10px;
  }
</style>
</head>
<body>
<main class="screen">
  <svg class="back" viewBox="0 0 16 18" aria-label="Back"><path d="M11 2 4 9l7 7" fill="none" stroke="#1fb4b1" stroke-width="2" stroke-linecap="round" stroke-linejoin="round"/></svg>

  <h1 class="login-title">Login</h1>
  <div class="login-field email"></div>
  <div class="login-field password"></div>
  <p class="forgot">Forgot password?</p>
  <div class="next-fab" aria-label="Continue">
    <svg width="26" height="14" viewBox="0 0 26 14"><path d="M1 7h23M18 1l6 6-6 6" fill="none" stroke="#fff" stroke-width="1.8" stroke-linecap="round" stroke-linejoin="round"/></svg>
  </div>

  <section class="recovery-card">
    <h2 class="recovery-title">Password Recovery</h2>
    <div class="email-input">Email Address</div>
    <p class="recovery-note">You will receive a password recovery<br>code on your email address.</p>
    <div class="recover-button">RECOVER</div>
  </section>

  <section class="keyboard">
    <div class="suggestions">
      <span class="suggestion" style="left:80px">Hi</span>
      <span class="suggestion-divider" style="left:126px"></span>
      <span class="suggestion" style="left:179px">Hello</span>
      <span class="suggestion-divider" style="left:232px"></span>
      <span class="suggestion" style="left:278px">Howdy</span>
      <svg class="mic" width="12" height="17" viewBox="0 0 12 17"><rect x="3.5" y="0.5" width="5" height="10" rx="2.5" fill="#5f6368"/><path d="M1 8a5 5 0 0 0 10 0M6 13v3" fill="none" stroke="#5f6368" stroke-width="1.5"/></svg>
    </div>
    <div class="key-row row-1">
      <span class="key">q<sup>1</sup></span><span class="key">w<sup>2</sup></span><span class="key">e<sup>3</sup></span><span class="key">r<sup>4</sup></span><span class="key">t<sup>5</sup></span><span class="key">y<sup>6</sup></span><span class="key">u<sup>7</sup></span><span class="key">i<sup>8</sup></span><span class="key">o<sup>9</sup></span><span class="key">p<sup>0</sup></span>
    </div>
    <div class="key-row row-2">
      <span class="key">a</span><span class="key">s</span><span class="key">d</span><span class="key">f</span><span class="key">g</span><span class="key">h</span><span class="key">j</span><span class="key">k</span><span class="key">l</span>
    </div>
    <div class="key-row row-3">
      <span class="key wide"><svg width="18" height="18" viewBox="0 0 18 18"><path d="M9 2 2 9.5h4v4h6v-4h4z" fill="#3c4043"/><rect x="6" y="15" width="6" height="1.8" fill="#3c4043"/></svg></span>
      <span class="key">z</span><span class="key">x</span><span class="key">c</span><span class="key">v</span><span class="key">b</span><span class="key">n</span><span class="key">m</span>
      <span class="key wide"><svg width="20" height="14" viewBox="0 0 20 14"><path d="M6 0h13a1 1 0 0 1 1 1v12a1 1 0 0 1-1 1H6L0 7z" fill="#3c4043"/><path d="M9.5 4l5 6M14.5 4l-5 6" stroke="#eef0f1" stroke-width="1.6"/></svg></span>
    </div>
    <div class="key-row row-4">
      <span class="key symbols">?123</span>
      <span class="key comma">,</span>
      <span class="key emoji"><svg width="16" height="16" viewBox="0 0 16 16"><circle cx="8" cy="8" r="7" fill="none" stroke="#3c4043" stroke-width="1.4"/></svg></span>
      <span class="space-bar"></span>
      <span class="key period">.</span>
      <span class="enter"><svg width="16" height="12" viewBox="0 0 16 12"><path d="M14 1v5H3M6 2.5 2.5 6 6 9.5" fill="none" stroke="#fff" stroke-width="1.8" stroke-linecap="round" stroke-linejoin="round"/></svg></span>
    </div>
  </section>
</main>
</body>
</html>
```